Business Card Design

We need a business card designed for a new company based in Melbourne called Kvt solutions. Kvt solutions provides management consulting specialising in the health and social services sector.

Kvt solutions offer a unique set of specialist skills │dealing with all levels of government │ unique communication skills│intimate knowledge of the health sector │solutions tailored to unique circumstances.

Kvt solutions takes on a select number of clients at any one time, this ensures that your organisation receives the attention required. On larger projects, Kvt solutions join up with other consultants to bring specialist skills to a project.
Updates

This is the first time I have used Pixel Harbor and thank you all for responding. The variation is amazing and makes it hard to decide. I have to ask some of my friends to give me their views. The response is fantastic. The one I pick will basically be the most visually appealing

Industry/Entity Type

Management Consulting

Contact Information for Business Card

Martin Oakes, Principal, Kvt solutions, 14 Wexcombe Ave, Larkdale VIC 3189, 0417 382 914, martino@kvtsolutions-example.com.au, www.kvtsolutions-example.com.au

```html
<!DOCTYPE html>
<html lang="en">
<head>
<meta charset="utf-8">
<title>Kvt solutions – Business Card</title>
<link rel="stylesheet" href="https://fonts.googleapis.com/css2?family=Arimo:ital,wght@0,400;0,700;1,700&display=swap">
<style>
  :root {
    --backdrop: #ece7e1;
    --card-red: #c00012;
    --band-black: #111111;
    --pattern-red: #c8173f;
    --pattern-pink: #d24a6c;
    --text-white: #ffffff;
    --text-black: #000000;
  }
  * { margin: 0; padding: 0; box-sizing: border-box; }
  html, body {
    width: 1200px;
    height: 798px;
    overflow: hidden;
    background: var(--backdrop);
  }
  .canvas {
    position: relative;
    width: 1200px;
    height: 798px;
  }
  .card {
    position: absolute;
    left: 108px;
    top: 95px;
    width: 985px;
    height: 608px;
    background: var(--card-red);
    font-family: "Arimo", Arial, sans-serif;
    color: var(--text-white);
    box-shadow: 0 4px 14px rgba(0,0,0,0.25);
  }
  .brand {
    position: absolute;
    left: 84px;
    top: 96px;
  }
  .brand-name {
    font-weight: 700;
    font-size: 44px;
    line-height: 1;
    letter-spacing: 1px;
    color: var(--text-white);
    white-space: nowrap;
  }
  .brand-tagline {
    margin-top: 20px;
    font-weight: 400;
    font-size: 13px;
    letter-spacing: 1.2px;
    color: var(--text-white);
    white-space: nowrap;
  }
  .person {
    position: absolute;
    right: 60px;
    top: 309px;
    text-align: right;
  }
  .person-name {
    font-size: 29px;
    font-weight: 400;
    letter-spacing: 0.5px;
    word-spacing: 6px;
    line-height: 1.1;
  }
  .person-title {
    font-size: 24px;
    font-weight: 700;
    font-style: italic;
    color: var(--text-black);
    line-height: 1.15;
  }
  .contact {
    position: absolute;
    right: 60px;
    top: 419px;
    text-align: right;
    font-size: 17px;
    line-height: 24px;
    letter-spacing: 0.3px;
    white-space: nowrap;
  }
  .contact-line {
    display: flex;
    justify-content: flex-end;
    align-items: center;
    gap: 8px;
  }
  .contact-item { display: inline-flex; align-items: center; gap: 8px; margin-left: 10px; }
  .contact-icon { width: 18px; height: 18px; flex: none; }
  .address { word-spacing: 2px; }
  .phone { word-spacing: 4px; }
  .divider {
    position: absolute;
    left: 0;
    top: 473px;
    width: 100%;
    height: 10px;
    background: var(--band-black);
  }
  .pattern-band {
    position: absolute;
    left: 0;
    top: 483px;
    width: 100%;
    height: 125px;
    background: linear-gradient(180deg, var(--pattern-red), var(--pattern-pink) 50%, var(--pattern-red));
  }
</style>
</head>
<body>
<div class="canvas">
  <section class="card">
    <div class="brand">
      <div class="brand-name">Kvt solutions</div>
      <div class="brand-tagline">HEALTH &amp; SOCIAL SERVICES CONSULTING</div>
    </div>

    <div class="person">
      <div class="person-name">Martin Oakes</div>
      <div class="person-title">Principal</div>
    </div>

    <div class="contact">
      <div class="address">14 Wexcombe Ave. Larkdale VIC 3189</div>
      <div class="contact-line">
        <span class="contact-item phone">
          <svg class="contact-icon" viewBox="0 0 18 18" aria-hidden="true">
            <rect x="6" y="2" width="6" height="14" rx="1.2" fill="none" stroke="#000" stroke-width="1.4"/>
            <line x1="8" y1="13.5" x2="10" y2="13.5" stroke="#000" stroke-width="1.2"/>
          </svg>
          0417 382 914
        </span>
        <span class="contact-item">
          <svg class="contact-icon" viewBox="0 0 22 18" style="width:22px" aria-hidden="true">
            <rect x="2" y="4" width="18" height="11" fill="none" stroke="#000" stroke-width="1.4"/>
            <polyline points="2,4 11,11 20,4" fill="none" stroke="#000" stroke-width="1.4"/>
          </svg>
          martin@kvtsolutions-example.com.au
        </span>
        <span class="contact-item">
          <svg class="contact-icon" viewBox="0 0 18 18" aria-hidden="true">
            <circle cx="9" cy="9" r="7.5" fill="none" stroke="#000" stroke-width="1.4"/>
            <ellipse cx="9" cy="9" rx="3.2" ry="7.5" fill="none" stroke="#000" stroke-width="1"/>
            <line x1="1.5" y1="9" x2="16.5" y2="9" stroke="#000" stroke-width="1"/>
          </svg>
          www.kvtsolutions-example.com
        </span>
      </div>
    </div>

    <div class="divider"></div>
    <div class="pattern-band" role="img" aria-label="Decorative red and pink crosshatch pattern band"></div>
  </section>
</div>
</body>
</html>
```